Stationary Set Rebrand for Brennick

We are a Canadian Distribution and Service Company that was established in 1969. Over the past 5 decades we have expanded our business and have warehouses across Canada. We specialize in adhesive tapes, adhesives, films, safety, warehouse, shipping, janitorial and packaging supplies.

We have updated our logo design and would like a new corporate branding identity that includes a new fresh Stationary Set (Business Cards, Letterhead, Letterhead MS Word, Envelope, Presentation Folders, Email Signatures, Notepad Covers, etc.)

Target Market(s)

Industrial Business Sector

Font styles to use
Sans Serif

Colors
0054AA
0677BA
7BADD7
CADEEF
E8F1F8
0094D4
00A9DD
6FCCEA
C7EBF8
E9F6FB
00AB8E
00BBA5
67D7C9
C6EFE9
E9F9F6
EB3D1F
EC4F4E
F09395
F8D3D4
FCEDEE

Requirements
Should not have
• Colors not too light, darker colours preferred

```html
<!DOCTYPE html>
<html lang="en">
<head>
<meta charset="utf-8">
<title>Brennick Business Card</title>
<link rel="stylesheet" href="https://fonts.googleapis.com/css2?family=Nunito:wght@400;600;800&display=swap">
<style>
  :root {
    --backdrop: #9a9a9a;
    --card: #1b1b1c;
    --card-deep: #111112;
    --accent: #eb3d1f;
    --accent-soft: #ec4f4e;
    --ink: #f2f2f2;
    --pattern-light: #5a5a5c;
    --pattern-dark: #161617;
  }
  * { box-sizing: border-box; margin: 0; padding: 0; }
  html, body {
    width: 1200px;
    height: 1083px;
    overflow: hidden;
    background: var(--backdrop);
    font-family: "Nunito", sans-serif;
  }
  .sheet {
    position: relative;
    width: 1200px;
    height: 1083px;
  }
  .card {
    position: absolute;
    left: 180px;
    width: 840px;
    height: 480px;
    background: var(--card);
    border-bottom: 5px solid var(--accent);
    box-shadow: 0 18px 40px rgba(0,0,0,0.35);
    overflow: hidden;
  }
  .card--front { top: 40px; }
  .card--back { top: 563px; background: var(--card-deep); }

  .brand {
    position: absolute;
    left: 60px;
    top: 0;
    width: 120px;
    height: 480px;
    display: flex;
    align-items: center;
    justify-content: center;
  }
  .brand__name {
    transform: rotate(-90deg);
    color: var(--ink);
    font-weight: 800;
    font-size: 64px;
    letter-spacing: 1px;
    white-space: nowrap;
  }

  .contact {
    position: absolute;
    left: 430px;
    top: 120px;
    color: var(--ink);
  }
  .contact__name {
    color: var(--accent-soft);
    font-weight: 600;
    font-size: 26px;
    letter-spacing: 1px;
    text-transform: uppercase;
  }
  .contact__title {
    font-size: 18px;
    margin-top: 2px;
  }
  .contact__address {
    font-size: 18px;
    line-height: 26px;
    margin-top: 22px;
  }
  .contact__list {
    list-style: none;
    margin-top: 20px;
    font-size: 18px;
    line-height: 30px;
  }
  .contact__list li {
    display: flex;
    align-items: center;
    gap: 10px;
  }
  .icon { width: 16px; height: 16px; flex: none; }

  .pattern {
    position: absolute;
    inset: 0;
    background: linear-gradient(120deg, var(--pattern-light) 0%, #2e2e30 40%, var(--pattern-dark) 70%);
  }
</style>
</head>
<body>
<main class="sheet">
  <section class="card card--front">
    <div class="brand">
      <span class="brand__name">Brennick</span>
    </div>
    <div class="contact">
      <h1 class="contact__name">Daniel Whitford</h1>
      <p class="contact__title">Development Manager Officer</p>
      <p class="contact__address">412 Harbour Line Road<br>Unit 88, Mississauga, ON L5T 2K9</p>
      <ul class="contact__list">
        <li>
          <svg class="icon" viewBox="0 0 16 16" aria-hidden="true"><path fill="#ec4f4e" d="M3.5 1.5l2.5 0 1 3.5-1.7 1.2a8 8 0 0 0 4.5 4.5L11 9l3.5 1v2.5c0 1-1 2-2 2A11 11 0 0 1 1.5 3.5c0-1 1-2 2-2z"/></svg>
          905-214-3370
        </li>
        <li>
          <svg class="icon" viewBox="0 0 16 16" aria-hidden="true"><rect x="1" y="3" width="14" height="10" rx="1" fill="#ec4f4e"/><path d="M1.5 3.5l6.5 5 6.5-5" fill="none" stroke="#1b1b1c" stroke-width="1.4"/></svg>
          d.whitford@brennicksupply.ca
        </li>
        <li>
          <svg class="icon" viewBox="0 0 16 16" aria-hidden="true"><g fill="none" stroke="#ec4f4e" stroke-width="1.3"><circle cx="8" cy="8" r="6.5"/><ellipse cx="8" cy="8" rx="3" ry="6.5"/><path d="M1.5 8h13M2.5 4.8h11M2.5 11.2h11"/></g></svg>
          brennicksupply.ca
        </li>
      </ul>
    </div>
  </section>

  <section class="card card--back">
    <div class="pattern" role="img" aria-label="Repeating glossy leaf pattern fading from grey to black, with one red leaf accent near the lower right"></div>
  </section>
</main>
</body>
</html>
```